Brand Identity Stationary Package

Hello I'm looking for a full branding package for my Property Management Company. I have a logo but looking to have the following
Business Card
Email signature
Facebook cover photo
Letterhead (word.doc)
#10 Envelope
Pocket Folder - link to 9x12 pocket folder design specs https://www.printorbit-example.ca/marketing-materials/presentation-folders
would like everything to match and be brand identifiable. The company looks after residential properties/apartments and some commercial properties. Attached is a zip of the files.
For Business Card
Name: Gareth Lindqvist
Position: Operations Manager
Number: 1 (555) 384-2917
Email: Gareth@harborkey-example.ca
Website: Harborkey-example.ca
Property Management

```html
<!DOCTYPE html>
<html lang="en">
<head>
<meta charset="utf-8">
<title>Harborkey Business Card</title>
<link href="https://fonts.googleapis.com/css2?family=Roboto:wght@400;500&family=Montserrat:wght@600&display=swap" rel="stylesheet">
<style>
  :root {
    --page: #141414;
    --card-top: #2b2b2b;
    --card-bottom: #1f1f1f;
    --card-back: #151515;
    --green: #7bc143;
    --white: #f2f2f2;
    --grey: #b5b5b5;
    --rule: #d9d9d9;
  }
  html, body {
    margin: 0;
    width: 1200px;
    height: 900px;
    overflow: hidden;
    background: var(--page);
    font-family: "Roboto", Arial, sans-serif;
  }
  .stage {
    position: relative;
    width: 1200px;
    height: 900px;
  }
  .card {
    position: absolute;
    left: 270px;
    width: 660px;
    height: 378px;
    border-radius: 3px;
    box-shadow: 0 12px 30px rgba(0,0,0,.55);
    overflow: hidden;
  }
  .card-front {
    top: 48px;
    background: linear-gradient(160deg, var(--card-top), var(--card-bottom));
  }
  .card-back {
    top: 474px;
    background: var(--card-back);
    display: flex;
    align-items: center;
    justify-content: center;
    flex-direction: column;
  }
  .accent-bar {
    position: absolute;
    left: 40px;
    top: 58px;
    width: 10px;
    height: 40px;
    background: var(--green);
  }
  .person {
    position: absolute;
    left: 70px;
    top: 92px;
  }
  .person-name {
    margin: 0;
    color: var(--green);
    font-size: 21px;
    font-weight: 500;
    letter-spacing: .5px;
    text-transform: uppercase;
  }
  .person-title {
    margin: 4px 0 0;
    color: var(--grey);
    font-size: 16px;
  }
  .divider {
    position: absolute;
    left: 252px;
    top: 130px;
    width: 338px;
    height: 1px;
    background: var(--rule);
  }
  .contact-list {
    position: absolute;
    left: 40px;
    top: 158px;
    margin: 0;
    padding: 0;
    list-style: none;
  }
  .contact-item {
    display: flex;
    align-items: center;
    gap: 12px;
    color: var(--grey);
    font-size: 16px;
    line-height: 30px;
  }
  .contact-icon {
    width: 16px;
    height: 16px;
    flex: none;
  }
  .brand-name {
    position: absolute;
    right: 66px;
    top: 70px;
    margin: 0;
    color: var(--white);
    font-family: "Montserrat", Arial, sans-serif;
    font-weight: 600;
    font-size: 40px;
    letter-spacing: 2px;
  }
  .office {
    position: absolute;
    right: 66px;
    bottom: 48px;
    text-align: right;
  }
  .office-company {
    margin: 0 0 4px;
    color: var(--green);
    font-size: 18px;
    font-weight: 500;
  }
  .office-address {
    margin: 0;
    color: var(--white);
    font-size: 18px;
    line-height: 26px;
    font-style: normal;
  }
  .back-brand {
    margin: 0;
    color: var(--white);
    font-family: "Montserrat", Arial, sans-serif;
    font-weight: 600;
    font-size: 54px;
    letter-spacing: 3px;
  }
  .back-web {
    margin: 26px 0 0;
    color: var(--grey);
    font-size: 18px;
    font-weight: 500;
  }
</style>
</head>
<body>
<main class="stage">
  <section class="card card-front">
    <div class="accent-bar"></div>
    <div class="person">
      <h1 class="person-name">Gareth Lindqvist</h1>
      <p class="person-title">Operations Manager</p>
    </div>
    <div class="divider"></div>
    <ul class="contact-list">
      <li class="contact-item">
        <svg class="contact-icon" viewBox="0 0 16 16"><path fill="#7bc143" d="M3.5 1.5l2.5 2.8-1.3 1.8c.9 2 2.6 3.7 4.6 4.6l1.8-1.3 2.8 2.5-1.4 2.1C7 13.6 2.4 9 1.4 2.9z"/></svg>
        1 (555) 384-2917
      </li>
      <li class="contact-item">
        <svg class="contact-icon" viewBox="0 0 16 16"><rect x="1" y="3" width="14" height="10" fill="#7bc143"/><path d="M1.5 3.5L8 9l6.5-5.5" fill="none" stroke="#222" stroke-width="1.2"/></svg>
        Gareth@harborkey-example.ca
      </li>
      <li class="contact-item">
        <svg class="contact-icon" viewBox="0 0 16 16" fill="none" stroke="#7bc143" stroke-width="1.3"><circle cx="8" cy="8" r="6.5"/><ellipse cx="8" cy="8" rx="3" ry="6.5"/><path d="M1.5 8h13"/></svg>
        www.harborkey-example.ca
      </li>
    </ul>
    <p class="brand-name">HARBORKEY</p>
    <div class="office">
      <p class="office-company">Harbor Key, Ltd</p>
      <address class="office-address">48 Cedar Brook Lane<br>Maple Ridge, ON L0X 1T5</address>
    </div>
  </section>

  <section class="card card-back">
    <p class="back-brand">HARBORKEY</p>
    <p class="back-web">www.harborkey-example.ca</p>
  </section>
</main>
</body>
</html>
```